Semi-anonymous photo sharing and messaging app

Design app interface. App is needed for semi-anonymous communication.

For instance if you are on a tour bus, and you just met some people there. You want to send them pictures, but you don't want to give your chatterbox / email / phone number. So instead you use this app - current name is "eLumix" but you can also suggest a name if it fits really well with the theme of the design.

The initial version of the app is in the vantor store
https://apps.vantorhub.example/store/apps/details?id=com.qz7mwplk3rt9bvne5hsyc

the web version of this app is located here
https://tallbluekites.example/

it is called Tall Blue Kites, because the password is four common words, and if you know those words, you can open the chat room.

As you can see app looks very poorly, and needs to be designed from bottom up. App should look nothing like it looks now. it should have original and easily recognizable feel to it.

I'm attaching screen-shots of the current app. Two screens - you enter password on one screen (or choose one of the existing "rooms") - you chat with peers on the second screen

It should be something neutral, so it's mainly for travellers, but could be used by anyone else. It should have vibe of comfort and security, but at the same time adventure and fun.

Please come back with more questions!

Target Market(s)

Travellers, mostly
single, groups,

Industry/Entity Type

Communication

Font styles to use
Sans Serif

Requirements
Must have
• original, light feel
• recognizable
• unique

```html
<!DOCTYPE html>
<html lang="en">
<head>
<meta charset="utf-8">
<title>Tall Blue Kites – Home</title>
<link href="https://fonts.googleapis.com/css2?family=Roboto:wght@300;400;500;700&display=swap" rel="stylesheet">
<style>
:root{
  --ink:#222222;
  --ink-soft:#444444;
  --green:#4e9c0c;
  --blue-top:#34a9f3;
  --blue-bottom:#1787df;
  --tab-blue:#1a90e4;
  --white:#ffffff;
  --bar:rgba(225,225,225,0.85);
}
*{box-sizing:border-box;margin:0;padding:0}
html,body{width:676px;height:1200px;overflow:hidden;background:#f2f2f2}
body{font-family:'Roboto',sans-serif;color:var(--ink)}
.screen{position:relative;width:676px;height:1200px;overflow:hidden}
.backdrop{position:absolute;inset:0;
  background:
    linear-gradient(180deg,rgba(255,255,255,0.55),rgba(255,255,255,0.55)),
    linear-gradient(135deg,#e9e2cf 0%,#e4e6e8 30%,#ece4dc 55%,#e2e3e4 75%,#efe6d6 100%)}
.status-bar{position:absolute;left:0;top:0;width:676px;height:50px;background:var(--bar);
  font-size:24px;display:flex;align-items:center;justify-content:space-between;padding:0 12px}
.status-left{display:flex;align-items:center;gap:6px}
.status-time{position:absolute;left:0;right:0;text-align:center;font-weight:500}
.status-right{display:flex;align-items:center;gap:8px}
.nav-bar{position:absolute;left:0;top:50px;width:676px;height:68px;background:var(--bar)}
.nav-title{position:absolute;left:0;right:0;top:25px;text-align:center;font-size:27px;font-weight:500;color:#333;line-height:1}
.mail-icon{position:absolute;left:34px;top:12px}
.settings-icon{position:absolute;left:600px;top:12px}
.avatar{position:absolute;left:242px;top:127px;width:192px;height:192px;border-radius:50%;
  border:6px solid var(--white);background:radial-gradient(circle at 50% 40%,#8a7864 0%,#5f6a4c 55%,#2c3a5e 100%)}
.welcome{position:absolute;left:0;right:0;top:334px;text-align:center;font-size:27px;font-weight:400}
.word-box{position:absolute;left:25px;top:427px;width:624px;height:85px;background:var(--white);
  border:1px solid #b9b9b9;border-radius:6px;display:flex;align-items:center}
.word{text-align:center;font-size:31px;font-weight:700;color:var(--green)}
.word + .word{border-left:2px solid #d4d4d4}
.word-box .word:nth-child(1){flex:0 0 160px}
.word-box .word:nth-child(2){flex:0 0 136px}
.word-box .word:nth-child(3){flex:0 0 132px}
.word-box .word:nth-child(4){flex:1}
.btn{position:absolute;display:flex;align-items:center;justify-content:center;color:var(--white);
  font-size:30px;font-weight:500;border-radius:3px;
  background:linear-gradient(180deg,var(--blue-top),var(--blue-bottom));box-shadow:0 2px 3px rgba(0,0,0,0.25)}
.btn-enter{left:232px;top:565px;width:197px;height:86px}
.btn-generate{left:173px;top:683px;width:314px;height:85px}
.recent{position:absolute;left:67px;top:806px;width:540px}
.recent-title{font-size:29px;font-weight:500;color:#333;margin-bottom:6px}
.recent-item{display:flex;justify-content:space-between;font-size:25px;font-weight:300;color:var(--ink-soft);height:38px;align-items:center}
.tab-bar{position:absolute;left:0;top:1100px;width:676px;height:100px;background:var(--tab-blue);display:flex}
.tab{flex:1;display:flex;flex-direction:column;align-items:center;justify-content:flex-end;padding-bottom:6px;
  color:var(--white);font-size:14.5px;font-weight:700;letter-spacing:0.3px}
.tab + .tab{border-left:1px solid rgba(255,255,255,0.35)}
.tab svg{margin-bottom:6px}
</style>
</head>
<body>
<div class="screen">
  <div class="backdrop" role="img" aria-label="Soft faded collage of travel and friendship photos"></div>

  <div class="status-bar">
    <div class="status-left">
      <svg width="80" height="14" viewBox="0 0 80 14"><circle cx="7" cy="7" r="6" fill="#222"/><circle cx="21" cy="7" r="6" fill="#222"/><circle cx="35" cy="7" r="6" fill="#222"/><circle cx="49" cy="7" r="5.5" fill="none" stroke="#222" stroke-width="1"/><circle cx="63" cy="7" r="5.5" fill="none" stroke="#222" stroke-width="1"/></svg>
      <span>AIRO</span>
      <svg width="24" height="18" viewBox="0 0 24 18"><path d="M2 6a14 14 0 0 1 20 0M5.5 9.5a9 9 0 0 1 13 0M9 13a4 4 0 0 1 6 0" fill="none" stroke="#222" stroke-width="2.2"/><circle cx="12" cy="16" r="1.8" fill="#222"/></svg>
    </div>
    <div class="status-time">4:21 PM</div>
    <div class="status-right">
      <svg width="14" height="22" viewBox="0 0 14 22"><path d="M2 6l10 9-5 5V2l5 5-10 9" fill="none" stroke="#777" stroke-width="1.8"/></svg>
      <span>100%</span>
      <svg width="52" height="22" viewBox="0 0 52 22"><rect x="1" y="2" width="45" height="18" rx="3" fill="none" stroke="#222" stroke-width="1.6"/><rect x="4" y="5" width="39" height="12" rx="1.5" fill="#222"/><rect x="47.5" y="8" width="3" height="6" fill="#222"/></svg>
    </div>
  </div>

  <div class="nav-bar">
    <svg class="mail-icon" width="64" height="42" viewBox="0 0 64 42"><rect x="2" y="9" width="48" height="31" fill="none" stroke="#333" stroke-width="2"/><path d="M2 9l24 18 24-18" fill="none" stroke="#333" stroke-width="2"/><circle cx="55" cy="9" r="8" fill="#eee" stroke="#333" stroke-width="1.5"/><text x="55" y="13" font-size="11" text-anchor="middle" fill="#333" font-family="Roboto,sans-serif">2</text></svg>
    <div class="nav-title">Tall Blue Kites</div>
    <svg class="settings-icon" width="46" height="46" viewBox="0 0 46 46"><path d="M23 3l4 1 1 5 4 2 4-3 3 3-3 4 2 4 5 1 1 4-1 4-5 1-2 4 3 4-3 3-4-3-4 2-1 5-4 1-4-1-1-5-4-2-4 3-3-3 3-4-2-4-5-1-1-4 1-4 5-1 2-4-3-4 3-3 4 3 4-2 1-5z" fill="none" stroke="#333" stroke-width="2" stroke-linejoin="round"/><circle cx="23" cy="23" r="8" fill="none" stroke="#333" stroke-width="2"/></svg>
  </div>

  <div class="avatar" role="img" aria-label="Profile photo of the user"></div>
  <p class="welcome">Welcome Marla Quinn!</p>

  <div class="word-box">
    <span class="word">Apple</span>
    <span class="word">Like</span>
    <span class="word">Ship</span>
    <span class="word">Wonder</span>
  </div>

  <div class="btn btn-enter">ENTER</div>
  <div class="btn btn-generate">GENERATE WORDS</div>

  <section class="recent">
    <h2 class="recent-title">Recent</h2>
    <div class="recent-item"><span>1. back, class, horse, husband.</span><span>x</span></div>
    <div class="recent-item"><span>2. amount, firm, industry, pupil.</span><span>x</span></div>
  </section>

  <nav class="tab-bar">
    <div class="tab">
      <svg width="58" height="58" viewBox="0 0 58 58"><circle cx="29" cy="29" r="27" fill="none" stroke="#fff" stroke-width="2"/></svg>
      KITES
    </div>
    <div class="tab">
      <svg width="56" height="52" viewBox="0 0 56 52"><path d="M3 3h50v34H24l-10 11v-11H3z" fill="none" stroke="#fff" stroke-width="2" stroke-linejoin="round"/><path d="M12 14h32M12 21h32M12 28h32" stroke="#fff" stroke-width="2"/></svg>
      CHAT ROOM
    </div>
    <div class="tab">
      <svg width="56" height="54" viewBox="0 0 56 54"><circle cx="28" cy="17" r="13" fill="none" stroke="#fff" stroke-width="2"/><path d="M4 52c0-13 10-20 24-20s24 7 24 20z" fill="none" stroke="#fff" stroke-width="2" stroke-linejoin="round"/></svg>
      PROFILE
    </div>
    <div class="tab">
      <svg width="58" height="58" viewBox="0 0 58 58"><circle cx="29" cy="29" r="27" fill="none" stroke="#fff" stroke-width="2"/><circle cx="29" cy="18" r="2" fill="#fff"/><path d="M29 25v17" stroke="#fff" stroke-width="2"/></svg>
      ABOUT
    </div>
  </nav>
</div>
</body>
</html>
```